Tamberlow Air Business Card Design

Design new, 2 sides, business cards for a residential and light commercial heating, air conditioning contractor.

Target Market(s)

Homeowners, small businesses

Industry/Entity Type

Business

Contact Information for Business Card

Dominic Westerhall
Phone - 862-415-2736
Email
Address - PO box 518
Brightwater NJ 07912
Website - www.HarborBreezeLLC.example

Requirements
Must have
• logo, company colors, standard size with no die cut, so I can use nova stamp

```html
<!DOCTYPE html>
<html lang="en">
<head>
<meta charset="utf-8">
<title>Tamberlow Air Business Card</title>
<link href="https://fonts.googleapis.com/css2?family=Open+Sans:wght@400;600;700&display=swap" rel="stylesheet">
<style>
  :root {
    --stage: #b9b9b9;
    --orange: #f28a33;
    --maroon: #a82238;
    --gold: #f5a01f;
    --white: #ffffff;
    --ink: #4a2a1a;
  }
  * { box-sizing: border-box; margin: 0; padding: 0; }
  html, body {
    width: 1200px; height: 950px; overflow: hidden;
    background: var(--stage);
    font-family: "Open Sans", Arial, sans-serif;
  }
  .sheet {
    width: 1200px; height: 950px;
    display: flex; flex-direction: column; align-items: center; justify-content: center;
    gap: 48px;
  }
  .card {
    position: relative;
    width: 720px; height: 411px;
    border-radius: 26px;
    overflow: hidden;
  }
  /* Front */
  .card-front {
    background: var(--orange);
    display: flex; flex-direction: column; align-items: center; justify-content: center;
  }
  .brand {
    display: flex; align-items: center; gap: 12px;
    color: var(--maroon);
    font-weight: 700;
    font-size: 46px;
    letter-spacing: 1px;
    text-transform: uppercase;
  }
  .brand-dot {
    width: 22px; height: 22px; border-radius: 50%;
    background: var(--maroon);
  }
  .tagline {
    margin-top: 30px;
    text-align: center;
    color: var(--ink);
    font-size: 17px;
    line-height: 1.4;
  }
  /* Back */
  .card-back { background: var(--maroon); }
  .card-back svg.backdrop { position: absolute; inset: 0; }
  .card-back .brand {
    position: absolute;
    left: 420px; top: 130px;
    width: 290px;
    flex-direction: column; gap: 4px;
    font-size: 38px; line-height: 1.05;
    text-align: center;
  }
  .contact {
    position: absolute; left: 44px; top: 140px;
    color: var(--white);
  }
  .person-name {
    color: var(--gold); font-weight: 700; font-size: 19px; letter-spacing: .5px;
  }
  .person-role { font-size: 14px; margin-top: 1px; }
  .address { margin-top: 30px; font-size: 14px; line-height: 1.45; }
  .lines { list-style: none; margin-top: 10px; font-size: 14px; }
  .lines li { display: flex; align-items: center; gap: 10px; line-height: 1.5; }
  .lines svg { width: 14px; height: 14px; fill: var(--gold); flex: none; }
</style>
</head>
<body>
<main class="sheet">

  <section class="card card-front">
    <div class="brand"><span class="brand-dot"></span>Tamberlow Air</div>
    <p class="tagline">Residential &amp; light commercial heating<br>Air conditioning contractor</p>
  </section>

  <section class="card card-back">
    <svg class="backdrop" width="720" height="411" viewBox="0 0 720 411">
      <circle cx="590" cy="170" r="279" fill="var(--gold)"/>
      <circle cx="590" cy="170" r="270" fill="var(--white)"/>
    </svg>

    <div class="brand"><span>Tamberlow</span><span>Air</span></div>

    <div class="contact">
      <p class="person-name">DOMINIC WESTERHALL</p>
      <p class="person-role">CEO/Founder</p>
      <p class="address">PO box 518<br>Brightwater NJ 07912</p>
      <ul class="lines">
        <li><svg viewBox="0 0 16 16"><path d="M3 1l3 3-1.5 2a9 9 0 0 0 5.5 5.5L12 10l3 3-2 2C6 15 1 10 1 3z"/></svg>862 415 2736</li>
        <li><svg viewBox="0 0 16 16"><path d="M4 0h8a1 1 0 0 1 1 1v14a1 1 0 0 1-1 1H4a1 1 0 0 1-1-1V1a1 1 0 0 1 1-1zm1 2v10h6V2z"/></svg>862 415 2790</li>
        <li><svg viewBox="0 0 16 16"><path d="M4 1h8v4H4zM1 6h14v7h-3v2H4v-2H1zm4 5v3h6v-3z"/></svg>862 415 2811</li>
        <li><svg viewBox="0 0 16 16"><path d="M1 3h14v10H1zm1 1v.5l6 4 6-4V4z"/></svg>dominic@tamberlowairllc.example</li>
        <li><svg viewBox="0 0 16 16"><path d="M8 1a7 7 0 1 0 0 14A7 7 0 0 0 8 1zm0 2a5 5 0 0 1 4.6 3H3.4A5 5 0 0 1 8 3zM3.4 10h9.2a5 5 0 0 1-9.2 0z"/></svg>www.TamberlowAirLLC.example</li>
      </ul>
    </div>
  </section>

</main>
</body>
</html>
```